Modernize Website: marcusfellwright.net

I am a novelist with an older-generation website at: marcusfellwright.net.

I am hoping to refresh this outdated website with a new, responsive redesign. I would prefer to host the code myself, and edit using Adobe Dreamweaver. So I’m not looking to use a hosted site builder like Plexo. Nor am I looking to use a CMS like Pagecraft.

In order to simplify the old site, there are a number of sections I’ll be looking to remove during this redesign. These are shown in the "MF Site Redesign" attachment. I can also provide imagery for new content (another book series in addition to the existing one), as well as higher-resolution imagery (if needed) of the old content.

Happy to answer any further questions.
Updates

I've uploaded a ZIP file containing high-res artwork associated with the new trilogy of books.

Target Market(s)

Readers of epic fantasy novels such as H.W.B. Castellane's THE WARDEN OF THE VALES, Harold P.Q. Ventris's A CROWN OF ASH AND RAIN, Victor Halloway's THE GATE OF STARS, or Dennis Vale's BLADE OF MERIVANE.

Industry/Entity Type

Entertainment

Coding

Coded - Design and coding required

Number of Pages Required

5+ page

Font styles to use
Serif
Decorative

Colors

Designer to choose colors to be used in the design.

Requirements
Must have
• I'm looking for a responsive design that displays nicely on both mobile and desktop devices. Existing site contains multiple pages, but these can obviously be combined into fewer pages (or even one) by divisions such as tabs, sections, and/or modal windows. See marcusfellwright.net for current content and "MF Site Redesign" attachment for content to be removed at this time.
Nice to have
• The ability to fulfill orders of autographed books directly from the website. I currently use Coinlo to do this, but it would be nice to incorporate a more comprehensive merchant service at a reasonable rate.
Should not have
• I'd like to host and control the site code myself. So please don't use a hosted web builder like Plexo, or a cloud-based CMS like Pagecraft.

```html
<!DOCTYPE html>
<html lang="en">
<head>
<meta charset="utf-8">
<title>Marcus Fellwright — The Chronicle of Veyrath</title>
<link href="https://fonts.googleapis.com/css2?family=Cinzel:wght@400;500&family=Lato:wght@400;700&family=Open+Sans:wght@400;600&display=swap" rel="stylesheet">
<style>
  :root {
    --ink: #07080b;
    --night: #0d1320;
    --night-mid: #1c2a40;
    --red-deep: #7e0008;
    --red: #c4000f;
    --red-bright: #e60019;
    --ember: #4a1a08;
    --ember-glow: #8a3a10;
    --slate: #141518;
    --stone: #3e3f43;
    --stone-light: #77787c;
    --white: #ffffff;
    --muted: #b9bcc2;
    --serif: "Cinzel", "Times New Roman", serif;
    --sans: "Lato", Arial, sans-serif;
    --body: "Open Sans", Arial, sans-serif;
  }
  * { margin: 0; padding: 0; box-sizing: border-box; }
  html, body { width: 1200px; height: 2311px; overflow: hidden; background: var(--ink); }
  .page { position: relative; width: 1200px; height: 2311px; overflow: hidden; color: var(--white); font-family: var(--sans); }
  .abs { position: absolute; }

  /* Header */
  .site-header { left: 0; top: 0; width: 1200px; height: 80px; background: linear-gradient(#000 0%, rgba(0,0,0,0.6) 60%, rgba(0,0,0,0) 100%); z-index: 3; }
  .brand { left: 117px; top: 12px; width: 303px; height: 117px; background: #050505; display: flex; align-items: center; gap: 14px; padding-left: 18px; z-index: 4; }
  .brand-mark { width: 14px; height: 14px; background: var(--red); flex: none; }
  .brand-name { font-family: var(--serif); font-size: 27px; line-height: 1.05; color: var(--white); font-weight: 400; }
  .main-nav { top: 49px; left: 568px; display: flex; z-index: 4; }
  .main-nav a { font-family: var(--sans); font-size: 16px; color: var(--white); text-decoration: none; text-transform: uppercase; position: absolute; white-space: nowrap; }
  .main-nav a.active { color: var(--red-bright); }

  /* Hero */
  .hero { left: 0; top: 0; width: 1200px; height: 740px; background:
      radial-gradient(ellipse 300px 480px at 600px 470px, #2a2a2e 0%, rgba(30,30,36,0.6) 45%, rgba(0,0,0,0) 75%),
      radial-gradient(ellipse 700px 420px at 560px 280px, var(--night-mid) 0%, var(--night) 55%, #05070c 100%); }
  .hero-art { left: 380px; top: 110px; width: 440px; height: 620px; border-radius: 200px 200px 40px 40px; background: radial-gradient(ellipse at 50% 35%, rgba(70,45,40,0.85) 0%, rgba(35,25,25,0.6) 50%, rgba(0,0,0,0) 80%); }
  .play { left: 559px; top: 299px; width: 80px; height: 80px; }
  .hero-title { left: 0; top: 394px; width: 1200px; text-align: center; font-family: var(--serif); font-size: 49px; font-weight: 400; letter-spacing: 0.5px; }
  .hero-sub { left: 250px; top: 461px; width: 700px; text-align: center; font-family: var(--sans); font-size: 23px; line-height: 31px; text-transform: uppercase; }

  /* Novels */
  .novels { left: 0; top: 660px; width: 1200px; height: 554px; }
  .section-title { left: 0; width: 1200px; text-align: center; font-family: var(--serif); font-size: 35px; font-weight: 400; }
  .novel-card { top: 867px; width: 308px; height: 262px; background: #0a0a0c; }
  .novel-card .art { position: absolute; inset: 0; }
  .novel-card .frame { position: absolute; left: 10px; top: 9px; right: 10px; bottom: 9px; border: 1px solid rgba(255,255,255,0.75); display: flex; align-items: center; justify-content: center; font-family: var(--serif); font-size: 24px; text-transform: uppercase; }

  /* Authors */
  .authors { left: 0; top: 1214px; width: 1200px; height: 442px; background: linear-gradient(#2a2a2c 0%, #151618 45%, #0a0a0b 100%); }
  .author { top: 1364px; width: 500px; height: 190px; }
  .author .portrait { position: absolute; left: 0; top: 0; width: 176px; height: 176px; border-radius: 50%; border: 2px solid #6b6d72; background: radial-gradient(circle at 50% 45%, #6a6560 0%, #3a3836 55%, #1c1c1d 100%); }
  .author .name { position: absolute; left: 193px; top: 0; font-family: var(--body); font-size: 20px; font-weight: 600; }
  .author .bio { position: absolute; left: 193px; top: 34px; width: 285px; font-family: var(--body); font-size: 14px; line-height: 21px; color: var(--muted); }
  .author .more { position: absolute; left: 193px; top: 149px; font-family: var(--body); font-size: 14px; color: var(--white); text-decoration: none; }
  .arrow { top: 1410px; width: 26px; height: 60px; }

  /* Worlds */
  .worlds { left: 0; top: 1656px; width: 1200px; height: 520px; background:
      radial-gradient(ellipse 380px 200px at 480px 40px, var(--ember-glow) 0%, rgba(90,35,10,0.5) 50%, rgba(0,0,0,0) 100%),
      radial-gradient(ellipse 160px 140px at 830px 300px, rgba(150,50,10,0.55) 0%, rgba(0,0,0,0) 100%),
      linear-gradient(var(--ember) 0%, #1e0b05 55%, #0b0604 100%); }
  .worlds-text { left: 300px; top: 1795px; width: 600px; text-align: center; font-family: var(--body); font-size: 15.5px; line-height: 26.5px; }
  .btn { left: 521px; top: 1953px; width: 149px; height: 41px; background: var(--red); color: var(--white); font-family: var(--sans); font-weight: 700; font-size: 14px; text-transform: uppercase; display: flex; align-items: center; justify-content: center; text-decoration: none; }

  /* Footer */
  .ridge { left: 0; top: 2060px; width: 1200px; height: 120px; }
  .site-footer { left: 0; top: 2168px; width: 1200px; height: 143px; background: linear-gradient(#3a3b3e 0%, #1d1e20 45%, #0e0e0f 100%); }
  .footer-nav a { position: absolute; top: 2207px; font-family: var(--sans); font-size: 15px; color: var(--white); text-decoration: none; text-transform: uppercase; }
  .copyright { left: 119px; top: 2242px; font-family: var(--sans); font-size: 11px; color: #9a9ca0; }
  .connect { left: 821px; top: 2208px; font-family: var(--sans); font-size: 16px; text-transform: uppercase; }
  .social { top: 2209px; width: 16px; height: 16px; border-radius: 50%; background: var(--white); }
</style>
</head>
<body>
<div class="page">

  <!-- Hero -->
  <section class="hero abs"></section>
  <div class="hero-art abs" role="img" aria-label="Illustration of an armoured masked warrior holding twin glowing blades"></div>

  <header class="site-header abs"></header>
  <a class="brand abs" href="#">
    <span class="brand-mark"></span>
    <span class="brand-name">Marcus<br>Fellwright</span>
  </a>
  <nav class="main-nav abs">
    <a class="active" href="#" style="left:0">Home</a>
    <a href="#" style="left:138px">Novels</a>
    <a href="#" style="left:249px">World</a>
    <a href="#" style="left:377px">Author</a>
  </nav>

  <svg class="play abs" viewBox="0 0 80 80" aria-label="Play trailer">
    <circle cx="40" cy="40" r="38" fill="#fff"/>
    <circle cx="40" cy="40" r="32" fill="none" stroke="#111" stroke-width="2.5"/>
    <path d="M33 27 L54 40 L33 53 Z" fill="#111"/>
  </svg>
  <h1 class="hero-title abs">The Chronicle of Veyrath</h1>
  <p class="hero-sub abs">Morbi ornare gravida elit integer congue augue et malesuada iaculis ipsum dui</p>

  <!-- Novels -->
  <svg class="novels abs" viewBox="0 0 1200 554" preserveAspectRatio="none" aria-hidden="true">
    <defs>
      <linearGradient id="redBand" x1="0" y1="0" x2="0" y2="1">
        <stop offset="0" stop-color="#7e0008"/>
        <stop offset="0.35" stop-color="#a8000c"/>
        <stop offset="1" stop-color="#e80019"/>
      </linearGradient>
    </defs>
    <path d="M0 64 L95 52 L200 12 L330 48 L470 58 L620 68 L760 46 L880 40 L995 10 L1110 40 L1200 58 L1200 554 L0 554 Z" fill="url(#redBand)"/>
  </svg>
  <h2 class="section-title abs" style="top:792px">Novels</h2>

  <a class="novel-card abs" href="#" style="left:117px">
    <span class="art" role="img" aria-label="Fantasy landscape of jagged mountains under a green sky" style="background:linear-gradient(160deg,#5a6a2a 0%,#2a3a2c 40%,#0f1a1c 100%)"></span>
    <span class="frame">Summaries</span>
  </a>
  <a class="novel-card abs" href="#" style="left:447px">
    <span class="art" role="img" aria-label="Dark throne hall with stairs and stone arches" style="background:radial-gradient(ellipse at 50% 55%,#4a4440 0%,#24201e 55%,#0c0b0b 100%)"></span>
    <span class="frame">Excerpts</span>
  </a>
  <a class="novel-card abs" href="#" style="left:775px">
    <span class="art" role="img" aria-label="Battle scene with a giant machine and burning ground" style="background:linear-gradient(165deg,#6a5a5a 0%,#5a3a30 45%,#7a3a12 75%,#2a1a12 100%)"></span>
    <span class="frame">Buy Online</span>
  </a>

  <!-- Authors -->
  <section class="authors abs"></section>
  <h2 class="section-title abs" style="top:1272px">Authors</h2>

  <svg class="arrow abs" style="left:46px" viewBox="0 0 26 60" aria-label="Previous"><path d="M24 2 L3 30 L24 58" fill="none" stroke="#fff" stroke-width="1.6"/></svg>
  <svg class="arrow abs" style="left:1113px" viewBox="0 0 26 60" aria-label="Next"><path d="M2 2 L23 30 L2 58" fill="none" stroke="#fff" stroke-width="1.6"/></svg>

  <article class="author abs" style="left:109px">
    <div class="portrait" role="img" aria-label="Author portrait photograph"></div>
    <h3 class="name">Author Name</h3>
    <p class="bio">aptent taciti sociosqu ad litora torquent per conubia nostra per inceptos hymenaeos Proin nulla arcu nonummy luctus dictum eget fermentum et lorem Nunc porta convallis pede</p>
    <a class="more" href="#">Read More</a>
  </article>
  <article class="author abs" style="left:603px; top:1370px">
    <div class="portrait" role="img" aria-label="Author portrait photograph"></div>
    <h3 class="name">Author Name</h3>
    <p class="bio">aptent taciti sociosqu ad litora torquent per conubia nostra per inceptos hymenaeos Proin nulla arcu nonummy luctus dictum eget fermentum et lorem Nunc porta convallis pede</p>
    <a class="more" href="#">Read More</a>
  </article>

  <!-- Worlds -->
  <section class="worlds abs" role="img" aria-label="Fiery dark fantasy world backdrop with a glowing rune circle"></section>
  <h2 class="section-title abs" style="top:1734px">Worlds</h2>
  <p class="worlds-text abs">aptent taciti sociosqu ad litora torquent per conubia nostra per inceptos hymenaeos Proin nulla arcu nonummy luctus dictum eget<br>Maecenas aliquet velit vel turpis Mauris neque metus malesuada nec ultricies sit amet porttitor mattis enim In massa libero interdum nec interdum vel blandit sed nulla In ullamcorpeceptos hymenaeos Proi</p>
  <a class="btn abs" href="#">Read More</a>

  <!-- Footer -->
  <svg class="ridge abs" viewBox="0 0 1200 120" preserveAspectRatio="none" aria-hidden="true">
    <defs>
      <linearGradient id="ridgeFill" x1="0" y1="0" x2="0" y2="1">
        <stop offset="0" stop-color="#6e6f73"/>
        <stop offset="1" stop-color="#3a3b3e"/>
      </linearGradient>
    </defs>
    <path d="M0 88 L200 78 L400 58 L540 38 L606 6 L680 40 L860 66 L1040 80 L1200 88 L1200 120 L0 120 Z" fill="#26272a"/>
    <path d="M0 112 L180 92 L340 70 L480 50 L606 14 L720 52 L900 82 L1080 100 L1200 108 L1200 120 L0 120 Z" fill="url(#ridgeFill)"/>
  </svg>
  <footer class="site-footer abs"></footer>
  <nav class="footer-nav">
    <a href="#" style="left:119px">Home</a>
    <a href="#" style="left:208px">Novels</a>
    <a href="#" style="left:310px">World</a>
    <a href="#" style="left:410px">Author</a>
  </nav>
  <p class="copyright abs">© 2018 Company Name&nbsp; All right reserved</p>
  <p class="connect abs">Connect</p>
  <a class="social abs" href="#" aria-label="Social link one" style="left:924px"></a>
  <a class="social abs" href="#" aria-label="Social link two" style="left:968px"></a>
  <a class="social abs" href="#" aria-label="Social link three" style="left:1013px"></a>
  <a class="social abs" href="#" aria-label="Social link four" style="left:1056px"></a>

</div>
</body>
</html>
```